Business Card for Multi-Brand Sportswear Company

We are looking for a business card which represents our company and the multiple brands within it.

The company: Fen Athletics (LTD)
The brands: Fen, TavaPuni, ElmStretch, Grit and Rain

Employees using these cards would be representing Fen Athletics, rather than any of the individual brands. You will see a current design within the uploaded files, to give some inspiration. The actual text of the brands is not necessary, but the logos should be on there is some format.

Our creative minds on this are stretched, so we are looking for someone to make this their own, and show us what a good business card should look like.

We may like to get these printed with spot gloss, so keep that in mind with your designs.

www.fenathletics.co.uk

Industry/Entity Type

Business

Contact Information for Business Card

Leo Pemberton-Hale
Operations Manager
(+44) 1632 960 418
Leo@fenathletics.co.uk
www.fenathletics.co.uk

Font styles to use
Sans Serif
Other font styles liked:
• Eurostile

Colors
ffffff

Requirements
Nice to have
• Dark (black) background

```html
<!DOCTYPE html>
<html lang="en">
<head>
<meta charset="utf-8">
<title>Fen Athletics – Business Card</title>
<link rel="stylesheet" href="https://fonts.googleapis.com/css2?family=Open+Sans:wght@400;600;700&display=swap">
<style>
  :root {
    --backdrop: #3a3532;
    --card-light: #f1f1f0;
    --card-dark: #0b0b0b;
    --ink: #2a2a2a;
    --ink-soft: #4a4a4a;
    --accent: #e0202a;
    --white: #ffffff;
    --brand-muted: #5e5366;
    --brand-grey: #8a8a8a;
  }
  * { box-sizing: border-box; margin: 0; padding: 0; }
  html, body { width: 1200px; height: 844px; overflow: hidden; }
  body {
    background: var(--backdrop);
    font-family: "Open Sans", Arial, sans-serif;
    display: flex;
    align-items: center;
    justify-content: center;
    gap: 60px;
  }
  .card {
    width: 520px;
    height: 300px;
    position: relative;
    border-radius: 3px;
    box-shadow: 0 10px 30px rgba(0,0,0,.45);
  }
  .card--front { background: var(--card-light); color: var(--ink); }
  .card--back { background: var(--card-dark); color: var(--white); }

  .wordmark {
    position: absolute;
    display: flex;
    align-items: center;
    gap: 12px;
    font-size: 32px;
    font-weight: 700;
    letter-spacing: .5px;
    white-space: nowrap;
  }
  .wordmark__dot {
    width: 18px; height: 18px; border-radius: 50%;
    background: var(--accent);
  }
  .card--front .wordmark { top: 56px; right: 40px; color: var(--ink); }
  .card--back .wordmark { top: 62px; left: 50%; transform: translateX(-50%); color: var(--white); }

  .contact__web {
    position: absolute; right: 40px; top: 118px;
    color: var(--accent); font-size: 13px;
  }
  .contact {
    position: absolute; left: 34px; right: 34px; bottom: 28px;
    font-size: 13px; line-height: 1.55; white-space: nowrap;
  }
  .contact__name { color: var(--accent); font-weight: 700; font-size: 16px; }
  .contact__role { color: var(--ink-soft); margin-bottom: 12px; }
  .contact__address { margin-bottom: 12px; }
  .contact__row { display: flex; gap: 22px; }
  .contact__label { color: var(--accent); font-weight: 600; }

  .brand-row {
    position: absolute; left: 30px; right: 30px; bottom: 50px;
    display: flex; justify-content: space-between; align-items: center;
  }
  .brand {
    display: flex; align-items: center; gap: 7px;
    font-size: 14px; font-weight: 600; color: var(--white); white-space: nowrap;
  }
  .brand__mark { width: 14px; height: 14px; }
  .brand__mark--square { background: var(--brand-muted); border-radius: 3px; }
  .brand__mark--red { background: var(--accent); }
  .brand__mark--circle { border-radius: 50%; background: var(--white); }
  .brand__mark--ring { border-radius: 50%; background: var(--brand-grey); }
</style>
</head>
<body>
  <section class="card card--front" aria-label="Business card front">
    <div class="wordmark"><span class="wordmark__dot"></span>Fen Athletics</div>
    <p class="contact__web">www.fenathletics.co.uk</p>
    <div class="contact">
      <p class="contact__name">Leo Pemberton-Hale</p>
      <p class="contact__role">Operations Manager</p>
      <p class="contact__address">Lower Field, Ashby Dale, Ridgeford, YO9 4LK</p>
      <div class="contact__row">
        <p><span class="contact__label">P:</span> (+44) 1632 960 418</p>
        <p><span class="contact__label">E:</span> Leo@fenathletics.co.uk</p>
      </div>
    </div>
  </section>

  <section class="card card--back" aria-label="Business card back">
    <div class="wordmark"><span class="wordmark__dot"></span>Fen Athletics</div>
    <div class="brand-row">
      <span class="brand"><span class="brand__mark brand__mark--square"></span>TavaPuni</span>
      <span class="brand"><span class="brand__mark brand__mark--red"></span>Grit and Rain</span>
      <span class="brand"><span class="brand__mark brand__mark--circle"></span>Fen</span>
      <span class="brand"><span class="brand__mark brand__mark--ring"></span>ElmStretch</span>
    </div>
  </section>
</body>
</html>
```